Design my site www.brieflyledger.com

So here is what I am thinking in terms of design:

https://plenvo.com

https://www.skyluxair.com

http://kalvex.com/harbor-plaza-tower/

I want the theme to be white and blue (royal blue). I attached a paint picture of what I would like the site to look like in terms of placing the text. Generally, what I like about the sites above is that they are simple, you can navigate easily and have some kind of idea of what's going on by looking at the center (picture and motto). Let's establish a clear understanding of how the functional part of the site would look like. Please see the picture attached.

I want to keep it simple: On top would be the Name 'BRIEFLY ledger", somewhere to the right on top on the page would be 'Sign in" button.

In the center would be a picture (maybe a video) with the Motto (on top of it all in capital) OBSERVE NAVIGATE DECIDE and below would be the "sign up now"

Below the picture (like on kalvex.com site) or to the left on top of the page would be "About Us', "Press" "Contact Us' buttons.

Then once the user gets to his page his got 3 tabs " Press Headlines", "Events", " Briefings".

we would keep the same format I only have on the site, but separate for every Tab.

I do not want the user to get distracted. I also want him to be able to access the page though mobile phone and be able to get automatic updates just like Zorvan Pings without having to sign in daily.

The landing page must be minimalist yet with business/corporate feel where users can navigate easily and a "what you see is what you get" approach. You want an image or video (personally I prefer the video.. it does capture the users attention instantly, as long as it is an interesting video), with your taglines in it.

Sections available to public: About Us, Contact Us, Landing Page with Signup Option

Private: Public Sections + User Account Page, Tabs for (Events, Press Headlines, Briefings)

Target Market(s)

PR/media monitoring/diplomatic community

Coding

Coded - Design and coding required

Number of Pages Required

1 page

Font styles to use
Serif
Sans Serif

Colors
0255a3
ec1f27

Requirements
Must have
• a simple landing page, that is user friendly.
Nice to have
• a video with the explanation of how to navigate the site
Should not have
• too many colors, graphs etc.

```html
<!DOCTYPE html>
<html lang="en">
<head>
<meta charset="utf-8">
<title>Briefly Ledger</title>
<link rel="stylesheet" href="https://fonts.googleapis.com/css2?family=Open+Sans:wght@400;600;700;800&display=swap">
<style>
  :root {
    --royal-blue: #0b4f9c;
    --white: #ffffff;
    --sky-top: #1c4562;
    --sky-mid: #5b6a72;
    --horizon: #b58a62;
    --city-mid: #6d5a48;
    --city-low: #3d3128;
    --shade: rgba(10, 14, 22, 0.28);
  }
  * { margin: 0; padding: 0; box-sizing: border-box; }
  html, body { width: 1200px; height: 640px; overflow: hidden; }
  body { font-family: "Open Sans", Arial, sans-serif; color: var(--white); }

  .landing {
    position: relative;
    width: 1200px;
    height: 640px;
    overflow: hidden;
  }
  .hero-image {
    position: absolute;
    inset: 0;
    background:
      linear-gradient(var(--shade), var(--shade)),
      linear-gradient(180deg, var(--sky-top) 0%, var(--sky-mid) 24%, var(--horizon) 46%, var(--city-mid) 66%, var(--city-low) 100%);
  }

  .sign-in {
    position: absolute;
    left: 979px;
    top: 13px;
    width: 88px;
    height: 30px;
    border: 1.5px solid var(--white);
    border-radius: 15px;
    display: flex;
    align-items: center;
    justify-content: center;
    font-size: 11.5px;
    font-weight: 700;
    letter-spacing: 0.3px;
    color: var(--white);
    text-decoration: none;
  }

  .brand {
    position: absolute;
    left: 328px;
    top: 186px;
    width: 544px;
    text-align: center;
    font-size: 49px;
    font-weight: 600;
    letter-spacing: 3px;
    line-height: 52px;
    text-transform: uppercase;
  }

  .motto {
    position: absolute;
    left: 329px;
    top: 261px;
    width: 544px;
    height: 53px;
    border-top: 1px solid rgba(255,255,255,0.85);
    border-bottom: 1px solid rgba(255,255,255,0.85);
    display: flex;
    align-items: center;
    justify-content: center;
    font-size: 30px;
    font-weight: 400;
  }

  .sign-up {
    position: absolute;
    left: 464px;
    top: 346px;
    width: 273px;
    height: 56px;
    border-radius: 28px;
    background: var(--royal-blue);
    display: flex;
    align-items: center;
    justify-content: center;
    gap: 16px;
    font-size: 21px;
    font-weight: 700;
    letter-spacing: 0.3px;
    color: var(--white);
    text-decoration: none;
  }
  .sign-up .divider { width: 1px; height: 22px; background: var(--white); }
  .sign-up svg { display: block; }

  .site-nav {
    position: absolute;
    left: 252px;
    top: 518px;
    display: flex;
    gap: 27px;
  }
  .site-nav a {
    width: 214px;
    height: 57px;
    border: 1.5px solid var(--white);
    border-radius: 29px;
    display: flex;
    align-items: center;
    justify-content: center;
    font-size: 21px;
    font-weight: 700;
    letter-spacing: 0.2px;
    color: var(--white);
    text-decoration: none;
  }
</style>
</head>
<body>
<main class="landing">
  <div class="hero-image" role="img" aria-label="Aerial photograph of a city skyline at sunset with a tall spired tower in the centre and a river beyond"></div>

  <a class="sign-in" href="#">SIGN IN</a>

  <h1 class="brand">Briefly Ledger</h1>
  <p class="motto">Observe Navigate Decide</p>

  <a class="sign-up" href="#">
    <span>SIGN UP NOW</span>
    <span class="divider"></span>
    <svg width="20" height="14" viewBox="0 0 20 14" aria-hidden="true">
      <path d="M0 5h11V0l9 7-9 7V9H0z" fill="#ffffff"/>
    </svg>
  </a>

  <nav class="site-nav">
    <a href="#">ABOUT US</a>
    <a href="#">PRESS</a>
    <a href="#">CONTACT US</a>
  </nav>
</main>
</body>
</html>
```